The Q Collective Business Cards

We need a sleek looking business card for our real estate company. Looking for a clean, modern, eye catching design on a standard size business card.
Updates

No more submissions please! Thank you!

Target Market(s)

General Public/Real Estate Clients

Industry/Entity Type

Real Estate

Contact Information for Business Card

Cards will be customized for each agent.

Colors

Designer to choose only greyscale colors for use in the design.

Requirements
Must have
• Black, white, gray color pallet, Photo area for headshot on the front of the card

```html
<!DOCTYPE html>
<html lang="en">
<head>
<meta charset="utf-8">
<title>The Q Collective – Business Card</title>
<link rel="stylesheet" href="https://fonts.googleapis.com/css2?family=Figtree:wght@600&family=Roboto:wght@400&display=swap">
<style>
  :root {
    --page-bg: #d9d6d2;
    --card-bg: #eeece9;
    --ink: #1c1c1c;
    --ink-soft: #2a2a2a;
    --photo-top: #c9b7a5;
    --photo-mid: #9c7a60;
    --photo-low: #d8c6b2;
  }
  * { box-sizing: border-box; margin: 0; padding: 0; }
  html, body {
    width: 1200px;
    height: 1054px;
    overflow: hidden;
    background: var(--page-bg);
  }
  .card {
    position: absolute;
    left: 100px;
    top: 224px;
    width: 1000px;
    height: 607px;
    background: var(--card-bg);
    border-radius: 26px;
    overflow: hidden;
    font-family: "Roboto", Arial, sans-serif;
    color: var(--ink);
  }
  .brand {
    position: absolute;
    left: 51px;
    top: 86px;
    width: 489px;
    display: flex;
    align-items: center;
    gap: 16px;
    white-space: nowrap;
  }
  .brand-mark {
    width: 20px;
    height: 20px;
    background: var(--ink);
    flex: none;
  }
  .brand-name {
    font-family: "Roboto", Arial, sans-serif;
    font-weight: 400;
    font-size: 38px;
    letter-spacing: 2px;
    color: var(--ink);
    text-transform: uppercase;
    line-height: 1;
  }
  .brand-tagline {
    position: absolute;
    left: 51px;
    top: 166px;
    width: 489px;
    text-align: center;
    font-size: 20px;
    letter-spacing: 6px;
    color: var(--ink);
  }
  .agent-name {
    position: absolute;
    left: 51px;
    top: 233px;
    font-family: "Figtree", Arial, sans-serif;
    font-weight: 600;
    font-size: 40px;
    color: var(--ink);
    white-space: nowrap;
  }
  .agent-role {
    position: absolute;
    left: 51px;
    top: 290px;
    font-size: 25px;
    color: var(--ink-soft);
  }
  .address {
    position: absolute;
    left: 51px;
    top: 370px;
    font-size: 25px;
    line-height: 38px;
    color: var(--ink-soft);
    font-style: normal;
  }
  .contacts {
    position: absolute;
    left: 51px;
    top: 452px;
    list-style: none;
    font-size: 25px;
    line-height: 38px;
    color: var(--ink-soft);
  }
  .contacts li {
    display: flex;
    align-items: center;
    gap: 28px;
    white-space: nowrap;
  }
  .contacts svg {
    width: 22px;
    height: 22px;
    fill: var(--ink);
    flex: none;
  }
  .headshot {
    position: absolute;
    right: 0;
    top: 0;
    width: 439px;
    height: 100%;
    background: linear-gradient(180deg, var(--photo-top) 0%, var(--photo-mid) 45%, var(--photo-low) 100%);
  }
</style>
</head>
<body>
  <section class="card">
    <div class="brand">
      <span class="brand-mark"></span>
      <span class="brand-name">The Q Collective</span>
    </div>
    <p class="brand-tagline">• REAL ESTATE TEAM •</p>

    <h1 class="agent-name">Dana Moreau Ellis</h1>
    <p class="agent-role">Real Estate Broker</p>

    <address class="address">
      4120 Magnolia Ave<br>
      Riverton, LA, US 70900
    </address>

    <ul class="contacts">
      <li>
        <svg viewBox="0 0 24 24" aria-hidden="true"><path d="M6.6 10.8a15.1 15.1 0 0 0 6.6 6.6l2.2-2.2a1 1 0 0 1 1-.25 11.4 11.4 0 0 0 3.6.57 1 1 0 0 1 1 1V20a1 1 0 0 1-1 1A17 17 0 0 1 3 4a1 1 0 0 1 1-1h3.5a1 1 0 0 1 1 1c0 1.25.2 2.45.57 3.57a1 1 0 0 1-.25 1z"/></svg>
        <span>+1 555-218-0937</span>
      </li>
      <li>
        <svg viewBox="0 0 24 24" aria-hidden="true"><path d="M2 5h20v14H2z M4 7v.4l8 5.2 8-5.2V7z" fill-rule="evenodd"/></svg>
        <span>dana@riverbendhomefinder.com</span>
      </li>
      <li>
        <svg viewBox="0 0 24 24" aria-hidden="true"><path d="M12 2a10 10 0 1 0 0 20 10 10 0 0 0 0-20zm6.9 6h-3a15 15 0 0 0-1.3-3.8A8 8 0 0 1 18.9 8zM12 4a13 13 0 0 1 1.9 4h-3.8A13 13 0 0 1 12 4zM4.3 14a8 8 0 0 1 0-4h3.4a16 16 0 0 0 0 4zm.8 2h3a15 15 0 0 0 1.3 3.8A8 8 0 0 1 5.1 16zm3-8h-3a8 8 0 0 1 4.3-3.8A15 15 0 0 0 8.1 8zM12 20a13 13 0 0 1-1.9-4h3.8A13 13 0 0 1 12 20zm2.3-6H9.7a14 14 0 0 1 0-4h4.6a14 14 0 0 1 0 4zm.3 5.8a15 15 0 0 0 1.3-3.8h3a8 8 0 0 1-4.3 3.8zm1.7-5.8a16 16 0 0 0 0-4h3.4a8 8 0 0 1 0 4z"/></svg>
        <span>www.riverbendhomefinder.com</span>
      </li>
    </ul>

    <div class="headshot" role="img" aria-label="Agent headshot photo area"></div>
  </section>
</body>
</html>
```